A fantastic website for a physio

We are looking for an eye catching website which can attract as many customer as possible.
We have logo designed and ready to be used in the website.
Please use the green and blue which is used in our logo for the preferred colors.
The following are the designs that I Iike:
http://www.example-clinicone.com.au/
http://www.example-rehabtwo.com.au/
We will be having other services including massage therapy, Psychology and podiatrist. You can find information about podiatry in our condition sheet.
for the address you can put Shop 5/248 Wattlebrook Street, Kelvindale. It might change but for now you can leave it until I confirm that in the next couple of days.

Logo file can be downloaded here:
https://files.example-share.net/s/qz4mtl9wkr82bvx/Logo1511.jpg?dl=0

Target Market(s)

Infant to old people.
We speak Farsi.

Industry/Entity Type

Physical Therapy

Number of Pages Required

5+ page

Font styles to use
Serif

Colors
33a6d7
abd037
e667a6

Requirements
Must have
• Home, About , our services, Conditions we treat and contact
• For home page and contacts we would like a tab that can connect to another website(bookwell) for online booking. We would like the patient's to be able to leave us massage or leave their email for monthly news letter. For the condition we treat you can use the condition sheets I have attached. For about us and home page you can use brochure I have attached.
• The other things should have include: in-line contact form, Location Map, clinic hours, newsletter sign-up etc, schema rich contact information
• Social media connection to our Facebook, Instagram and linked in
Nice to have
• Search engine optimization for Merrylands and Parramatta physiotherapy.
• We can speak English and Farsi. So is nice to have an information tab for Farsi speaking people. I can provide you with the texts.

```html
<!DOCTYPE html>
<html lang="en">
<head>
<meta charset="utf-8">
<title>Harbourline Physiotherapy</title>
<link rel="stylesheet" href="https://fonts.googleapis.com/css2?family=Raleway:wght@500;600;700&family=Open+Sans:ital,wght@0,400;0,600;0,700;1,400;1,600&display=swap">
<style>
:root{
  --blue:#33a6d7;
  --blue-deep:#1e93cf;
  --green:#abd037;
  --green-deep:#93bd24;
  --pink:#e667a6;
  --ink:#333;
  --text:#555;
  --muted:#888;
  --white:#fff;
}
*{margin:0;padding:0;box-sizing:border-box}
html,body{width:1200px;height:2390px;overflow:hidden;background:var(--white)}
body{position:relative;font-family:"Open Sans",Arial,sans-serif;color:var(--text)}
.abs{position:absolute}
.heading-font{font-family:"Raleway",Arial,sans-serif}

/* header */
.top-strip{left:0;top:0;width:1200px;height:4px;display:flex}
.top-strip span{flex:1}
.site-header{left:0;top:4px;width:1200px;height:86px;background:var(--white)}
.brand{left:160px;top:20px;display:flex;align-items:center;gap:10px}
.brand-dot{width:46px;height:46px;border-radius:50%;background:var(--blue)}
.brand-name{font-family:"Raleway",sans-serif;font-weight:700;font-size:22px;line-height:1.05;color:var(--blue)}
.main-nav{top:37px;left:0;width:1200px;font-family:"Raleway",sans-serif;font-weight:700;font-size:12px;color:#222}
.main-nav a{position:absolute;text-decoration:none;color:inherit;white-space:nowrap}
.main-nav a.active{color:var(--green)}
.lang{top:26px;width:36px;height:36px;border-radius:50%;border:2px solid;font:700 12px "Open Sans",sans-serif;display:flex;align-items:center;justify-content:center}

/* hero */
.hero{left:0;top:90px;width:1200px;height:572px;background:linear-gradient(100deg,#eef3f5 0%,#e3ecf0 35%,#d9b7a8 55%,#9ec2de 75%,#dfe9ef 100%)}
.hero-title{left:160px;top:230px;font-family:"Raleway",sans-serif;font-weight:700;font-size:35px;line-height:42px}
.hero-title .l1{color:var(--green)}
.hero-title .l2{color:var(--blue)}
.hero-copy{left:160px;top:330px;width:370px;font-size:13.5px;line-height:23px;color:#444}
.hero-copy em{color:var(--green-deep);font-weight:600}
.btn{display:flex;align-items:center;justify-content:center;gap:6px;color:var(--white);font:700 11px "Open Sans",sans-serif;text-transform:uppercase;border-radius:2px}
.btn svg{width:12px;height:12px}
.btn-green{background:var(--green)}
.btn-blue{background:var(--blue)}
.btn-pink{background:var(--pink)}
.slider-arrow{top:334px;width:32px;height:32px;border-radius:50%;border:1px solid rgba(255,255,255,.8);display:flex;align-items:center;justify-content:center}

/* services */
.services{left:161px;top:598px;width:877px;height:237px;display:flex}
.service{flex:1;text-align:center;color:var(--white);padding-top:19px}
.service.massage{background:linear-gradient(90deg,#2c9bd6,#3eaee0)}
.service.psychology{background:linear-gradient(90deg,#8fbf25,#b4d63c)}
.service.podiatry{background:linear-gradient(90deg,#e0589b,#ec7db4)}
.service-icon{width:84px;height:84px;border-radius:50%;background:var(--white);margin:0 auto;display:flex;align-items:center;justify-content:center}
.service-icon span{width:38px;height:38px;border-radius:50%}
.service h3{font-family:"Raleway",sans-serif;font-weight:600;font-size:18px;margin-top:30px;letter-spacing:.3px}
.service p{font-size:10.5px;line-height:20px;margin:12px auto 0;width:230px;opacity:.95}

/* section heading */
.sec-head{display:flex;align-items:center;gap:10px}
.sec-mark{width:38px;height:38px;border-radius:50%}
.sec-title{font-family:"Raleway",sans-serif;font-weight:600;font-size:22px;color:#333;padding-bottom:4px;border-bottom:2px solid var(--green)}

/* about */
.about-copy{left:161px;top:928px;width:462px;font-size:10.6px;line-height:20.5px;color:#444}
.video{left:666px;top:878px;width:372px;height:248px;background:linear-gradient(135deg,#5b6066,#8d8f92 40%,#c9c1b8 70%,#6f7377)}
.play{left:830px;top:980px;width:44px;height:44px;border-radius:50%;background:#e02727;display:flex;align-items:center;justify-content:center}

/* contact band */
.contact-band{left:0;top:1148px;width:1200px;height:446px}
.form-field{background:var(--white);border-radius:2px;font:italic 10px "Open Sans",sans-serif;color:#777;padding:12px 12px}
.bookwell{left:286px;top:1472px;font-family:"Open Sans",sans-serif;font-weight:600;font-size:24px;color:var(--white);display:flex;align-items:center;gap:8px}
.bookwell i{width:26px;height:26px;border-radius:50%;background:var(--white);display:block}

/* blog */
.card-img{top:1679px;width:268px;height:164px}
.date{top:1679px;width:46px;height:58px;color:var(--white);text-align:center;font-family:"Raleway",sans-serif}
.date small{display:block;font-size:9px;padding-top:6px}
.date b{display:block;font-size:24px;line-height:28px;font-weight:700}
.card-title{top:1864px;width:268px;font-family:"Raleway",sans-serif;font-weight:500;font-size:17px;line-height:24px}
.card-text{top:1920px;width:268px;font-size:10.5px;line-height:19px;color:#333}

/* footer */
.footer{left:0;top:2052px;width:1200px;height:248px;background:linear-gradient(180deg,var(--blue-deep),#1a8ccc);border-top:4px solid var(--green)}
.f-head{top:2104px;font-family:"Raleway",sans-serif;font-weight:700;font-size:15px;color:var(--white)}
.f-input{width:189px;height:35px;background:var(--white);border-radius:2px;font:italic 10px "Open Sans",sans-serif;color:#666;padding:11px 10px}
.hours{left:386px;top:2139px;font-size:10.5px;color:var(--white);line-height:20.3px}
.hours li{list-style:none;display:flex}
.hours li::before{content:"\203A";width:22px;font-weight:700}
.hours .day{width:78px}
.contact-list{left:623px;top:2139px;font-size:10.5px;color:var(--white);line-height:20.3px}
.contact-list li{list-style:none;display:flex;gap:8px}
.contact-list svg{width:11px;height:11px;margin-top:5px;flex:none}
.map{left:802px;top:2142px;width:236px;height:130px;background:linear-gradient(135deg,#e9ecef,#dde3d7 50%,#eceae4)}
.bottom-bar{left:0;top:2300px;width:1200px;height:90px;background:var(--green)}
.social{top:2327px;width:38px;height:38px;border-radius:50%;border:2px solid var(--white)}
.foot-brand{left:520px;top:2322px;display:flex;align-items:center;gap:8px}
.foot-brand i{width:40px;height:40px;border-radius:50%;background:var(--white);display:block}
.foot-brand span{font-family:"Raleway",sans-serif;font-weight:700;font-size:17px;line-height:1.05;color:var(--white)}
.copyright{right:162px;top:2330px;text-align:right;font-size:10.5px;line-height:17px;color:var(--white)}
</style>
</head>
<body>

<div class="abs top-strip"><span style="background:var(--blue)"></span><span style="background:var(--green)"></span><span style="background:var(--pink)"></span></div>

<header class="abs site-header">
  <div class="abs brand" style="top:16px"><span class="brand-dot"></span><span class="brand-name">Harbourline<br>Physiotherapy</span></div>
  <nav class="abs main-nav">
    <a class="active" style="left:475px">HOME</a>
    <a style="left:542px">ABOUT US</a>
    <a style="left:631px">SERVICES</a>
    <a style="left:717px">CONDITIONS WE TREAT</a>
    <a style="left:883px">CONTACT</a>
  </nav>
  <span class="abs lang" style="left:964px;border-color:var(--green);color:var(--green)">EN</span>
  <span class="abs lang" style="left:1002px;border-color:#444;color:#444">FA</span>
</header>

<section class="abs hero" role="img" aria-label="Photo of a physiotherapist treating the shoulder of a smiling senior woman in a clinic"></section>
<div class="abs slider-arrow" style="left:32px"><svg width="10" height="10" viewBox="0 0 10 10"><path d="M6.5 1.5 3 5l3.5 3.5" fill="none" stroke="#fff" stroke-width="1.5"/></svg></div>
<div class="abs slider-arrow" style="left:1130px"><svg width="10" height="10" viewBox="0 0 10 10"><path d="M3.5 1.5 7 5 3.5 8.5" fill="none" stroke="#fff" stroke-width="1.5"/></svg></div>
<h1 class="abs hero-title"><span class="l1" style="display:block">Harbourline</span><span class="l2" style="display:block">PHYSIOTHERAPY</span></h1>
<p class="abs hero-copy">Sed ut perspiciatis unde omnis isteuerror sit voluptatem accusantium dolor emq <em>ueloudantium, totam reers</em> pici atis unde omnis isteuerror sit voluptatem accusantiu</p>
<a class="abs btn btn-green" style="left:161px;top:418px;width:107px;height:34px">Read more <svg viewBox="0 0 12 12"><circle cx="6" cy="6" r="5" fill="none" stroke="#fff" stroke-width="1.4"/><path d="M5 3.5 7.5 6 5 8.5" fill="none" stroke="#fff" stroke-width="1.4"/></svg></a>

<section class="abs services">
  <div class="service massage">
    <div class="service-icon" role="img" aria-label="Massage therapy icon"><span style="background:var(--blue)"></span></div>
    <h3>MASSAGE THERAPY</h3>
    <p>Sor sit voluptatem accusantium doloremqu dan tium, totam rem Sor sit voluptatem accusa ntium doloremque laudan tiloum.</p>
  </div>
  <div class="service psychology">
    <div class="service-icon" role="img" aria-label="Psychology icon"><span style="background:var(--green)"></span></div>
    <h3>PSYCHOLOGY</h3>
    <p>Sor sit voluptatem accusantium doloremqu dan tium, totam rem Sor sit voluptatem accusa ntium doloremque laudan tiloum.</p>
  </div>
  <div class="service podiatry">
    <div class="service-icon" role="img" aria-label="Podiatry icon"><span style="background:var(--pink)"></span></div>
    <h3>PODIATRIST</h3>
    <p>Sor sit voluptatem accusantium doloremqu dan tium, totam rem Sor sit voluptatem accusa ntium doloremque laudan tiloum.</p>
  </div>
</section>

<div class="abs sec-head" style="left:161px;top:870px"><span class="sec-mark" style="background:var(--blue)"></span><h2 class="sec-title">HARBOURLINE PHYSIOTHERAPY</h2></div>
<p class="abs about-copy">Lorem ipsum dolor sit amet, consectetur adipiscing elit, sed do eiusmod tempor incididunt ut labore et dolore magna aliquat enim ad minim veniam, quis nostrud exercitation ullamco laboris nisi ut aliquip ex ea commodo consequat. Duis aute irure dolor in reprehenderit in voluptate orem ipsum dolor sit amet, consectetur adipiscing elit, sed do eiusmod tempor incididunt ut labore et dolore magna aliqua. Ut enim ad minim veniam, quis nostrud exercitation ullamco laboris nisi ut aliquip ex ea commodo consequat.uis aute irure dolor in reprehenderit in voluptateLorem ipsum dolor sit amet, consectetur adipiscing eli.</p>
<a class="abs btn btn-green" style="left:161px;top:1088px;width:117px;height:38px">Get started <svg viewBox="0 0 12 12"><circle cx="6" cy="6" r="5" fill="none" stroke="#fff" stroke-width="1.4"/><path d="M5 3.5 7.5 6 5 8.5" fill="none" stroke="#fff" stroke-width="1.4"/></svg></a>
<div class="abs video" role="img" aria-label="Video still of a therapist stretching a patient's leg on a treatment table"></div>
<div class="abs play"><svg width="16" height="18" viewBox="0 0 16 18"><path d="M2 1l13 8-13 8z" fill="#fff"/></svg></div>
<svg class="abs" style="left:992px;top:886px" width="40" height="14" viewBox="0 0 40 14"><circle cx="3" cy="7" r="2" fill="#fff"/><circle cx="11" cy="3" r="2" fill="#fff"/><circle cx="11" cy="11" r="2" fill="#fff"/><path d="M3 7 11 3M3 7l8 4" stroke="#fff" stroke-width="1.2"/><circle cx="25" cy="7" r="5" fill="#fff"/><rect x="24.2" y="6" width="1.6" height="4" fill="#555"/><circle cx="25" cy="4.3" r=".9" fill="#555"/></svg>

<div class="abs contact-band" role="img" aria-label="Photo of a young woman doing a stretch on the grass in a sunny green park">
  <svg width="1200" height="446" viewBox="0 0 1200 446">
    <defs>
      <linearGradient id="parkTone" x1="0" y1="0" x2="1" y2="1">
        <stop offset="0" stop-color="#6f9a6e"/><stop offset=".35" stop-color="#a9c9a3"/><stop offset=".6" stop-color="#c7d7b8"/><stop offset="1" stop-color="#4f8f3a"/>
      </linearGradient>
    </defs>
    <path d="M0 0 Q600 80 1200 0 V430 Q600 360 0 430Z" fill="url(#parkTone)"/>
  </svg>
</div>
<div class="abs sec-head" style="left:161px;top:1258px"><span class="sec-mark" style="background:var(--white)"></span><h2 class="sec-title" style="color:var(--white)">QUICK CONTACT FORM</h2></div>
<div class="abs form-field" style="left:161px;top:1328px;width:241px;height:40px">Name:</div>
<div class="abs form-field" style="left:161px;top:1372px;width:241px;height:40px">Email:</div>
<div class="abs form-field" style="left:161px;top:1417px;width:241px;height:40px">Phone:</div>
<div class="abs form-field" style="left:408px;top:1328px;width:271px;height:129px">Message:</div>
<a class="abs btn btn-pink" style="left:161px;top:1468px;width:118px;height:38px">Submit here <svg viewBox="0 0 12 12"><circle cx="6" cy="6" r="5" fill="none" stroke="#fff" stroke-width="1.4"/><path d="M5 3.5 7.5 6 5 8.5" fill="none" stroke="#fff" stroke-width="1.4"/></svg></a>
<div class="abs bookwell">bookwell <i></i></div>

<div class="abs sec-head" style="left:460px;top:1592px"><span class="sec-mark" style="background:var(--green)"></span><h2 class="sec-title">RECENT BLOG POSTS</h2></div>

<div class="abs card-img" style="left:161px;background:linear-gradient(135deg,#b06a5a,#e9a9a3 50%,#8c6f68)" role="img" aria-label="Photo of two women talking in a counselling session"></div>
<div class="abs date" style="left:161px;background:var(--blue)"><small>Oct</small><b>20</b></div>
<h3 class="abs card-title" style="left:161px;color:var(--blue)">Lorem ipsum dolor sit loameut consectetur adipiscing.</h3>
<p class="abs card-text" style="left:161px">Lorem ipsum dolor sit amet, consectetur a lordipiscig elit, sed do eiusmod tempor incididunt ut lablkoeoret dolore magna aliqua enim ad minim veniam.</p>
<a class="abs btn btn-blue" style="left:161px;top:1981px;width:107px;height:36px">Read more <svg viewBox="0 0 12 12"><circle cx="6" cy="6" r="5" fill="none" stroke="#fff" stroke-width="1.4"/><path d="M5 3.5 7.5 6 5 8.5" fill="none" stroke="#fff" stroke-width="1.4"/></svg></a>

<div class="abs card-img" style="left:467px;background:linear-gradient(135deg,#8fd3c8,#e7d4c8 50%,#f1efee)" role="img" aria-label="Photo of a therapist examining a patient's shoulder"></div>
<div class="abs date" style="left:467px;background:var(--green)"><small>Oct</small><b>20</b></div>
<h3 class="abs card-title" style="left:467px;color:var(--green-deep)">Lorem ipsum dolor sit loameut consectetur adipiscing.</h3>
<p class="abs card-text" style="left:467px">Lorem ipsum dolor sit amet, consectetur a lordipiscig elit, sed do eiusmod tempor incididunt ut lablkoeoret dolore magna aliqua enim ad minim veniam.</p>
<a class="abs btn btn-green" style="left:467px;top:1981px;width:107px;height:36px">Read more <svg viewBox="0 0 12 12"><circle cx="6" cy="6" r="5" fill="none" stroke="#fff" stroke-width="1.4"/><path d="M5 3.5 7.5 6 5 8.5" fill="none" stroke="#fff" stroke-width="1.4"/></svg></a>

<div class="abs card-img" style="left:772px;background:linear-gradient(135deg,#d9c2a4,#e37c5b 50%,#b8a690)" role="img" aria-label="Photo of a therapist stretching a patient's leg in a gym"></div>
<div class="abs date" style="left:772px;background:var(--pink)"><small>Oct</small><b>20</b></div>
<h3 class="abs card-title" style="left:772px;color:var(--pink)">Lorem ipsum dolor sit loameut consectetur adipiscing.</h3>
<p class="abs card-text" style="left:772px">Lorem ipsum dolor sit amet, consectetur a lordipiscig elit, sed do eiusmod tempor incididunt ut lablkoeoret dolore magna aliqua enim ad minim veniam.</p>
<a class="abs btn btn-pink" style="left:772px;top:1981px;width:107px;height:36px">Read more <svg viewBox="0 0 12 12"><circle cx="6" cy="6" r="5" fill="none" stroke="#fff" stroke-width="1.4"/><path d="M5 3.5 7.5 6 5 8.5" fill="none" stroke="#fff" stroke-width="1.4"/></svg></a>

<footer class="abs footer"></footer>
<h4 class="abs f-head" style="left:161px">NEWSLETTER SIGN-UP</h4>
<div class="abs f-input" style="left:161px;top:2142px">Name:</div>
<div class="abs f-input" style="left:161px;top:2182px">Email Address:</div>
<a class="abs btn btn-green" style="left:161px;top:2225px;width:99px;height:37px;font-size:11.5px">Subscribe</a>

<h4 class="abs f-head" style="left:386px">CLINIC HOURS</h4>
<ul class="abs hours">
  <li><span class="day">Monday</span>7:00 AM - 7:00 PM</li>
  <li><span class="day">Tuesday</span>7:00 AM - 7:00 PM</li>
  <li><span class="day">Wednesday</span>7:00 AM - 7:00 PM</li>
  <li><span class="day">Thursday</span>7:00 AM - 7:00 PM</li>
  <li><span class="day">Friday</span>7:00 AM - 7:00 PM</li>
  <li><span class="day">Saturday</span>8:00 AM - 3:00 PM</li>
  <li><span class="day">Sunday</span>Closed</li>
</ul>

<h4 class="abs f-head" style="left:623px">CONTACT US</h4>
<ul class="abs contact-list">
  <li><svg viewBox="0 0 12 12"><path d="M6 .5a4 4 0 0 0-4 4c0 3 4 7 4 7s4-4 4-7a4 4 0 0 0-4-4zm0 5.5a1.5 1.5 0 1 1 0-3 1.5 1.5 0 0 1 0 3z" fill="#fff"/></svg><span>Shop 5/248 Wattlebrook Street,<br>Kelvindale</span></li>
  <li style="margin-top:20px"><svg viewBox="0 0 12 12"><path d="M2.5 1 4.5 1 5.5 3.5 4 4.7a7 7 0 0 0 3.3 3.3L8.5 6.5 11 7.5v2a1.5 1.5 0 0 1-1.5 1.5A9 9 0 0 1 1 2.5 1.5 1.5 0 0 1 2.5 1z" fill="#fff"/></svg><span>Phone:+61.400 123 456</span></li>
  <li><svg viewBox="0 0 12 12"><rect x="1" y="4" width="10" height="6" fill="#fff"/><rect x="3" y="1" width="6" height="3" fill="#fff"/></svg><span>Fax: 900-555-0142</span></li>
  <li><svg viewBox="0 0 12 12"><rect x="1" y="2.5" width="10" height="7" fill="#fff"/><path d="M1 3l5 3.5L11 3" fill="none" stroke="#1e93cf" stroke-width="1"/></svg><span>hello@example-harbourline.com</span></li>
</ul>

<h4 class="abs f-head" style="left:802px">LOCATION MAP</h4>
<div class="abs map" role="img" aria-label="Street map showing the clinic location"></div>

<div class="abs bottom-bar"></div>
<span class="abs social" style="left:161px;background:var(--blue)" role="img" aria-label="Video channel"></span>
<span class="abs social" style="left:211px" role="img" aria-label="Social profile"></span>
<span class="abs social" style="left:261px" role="img" aria-label="Photo profile"></span>
<span class="abs social" style="left:311px" role="img" aria-label="Microblog profile"></span>
<span class="abs social" style="left:361px" role="img" aria-label="Social page"></span>
<div class="abs foot-brand"><i></i><span>Harbourline<br>Physiotherapy</span></div>
<p class="abs copyright">© 2016 All copyrights reserved.Harbourline Physiotherapy.<br>Privacy Policy And Terms And Conditions</p>

</body>
</html>
```